Willow Cradle Pregnancy and Baby Massage

I need a web design for a new business, WILLOW CRADLE PREGNANCY AND BABY MASSAGE that I am in the process of setting up in the suburbs of Perth, Western Australia. The business is owned and operated by myself and my intention is to service Pregnant Mothers and Parents of Young Babies that would benefit from massage. I would like to have a "Home Page" and pages for "About Me", "Pregnancy Massage", "Baby Massage", a Pricing Page for Pregnancy Massage Sessions, a Pricing Page for Baby Massage Sessions, and a "Contact Me" page to allow clients to either contact me with queries or book available pregnancy massage sessions on a particular day of the week. I would also like a "News" page that would include articles I have written, news about new courses and a link to my Facebook page (yet to be set up). I would like to keep the colour schemes similar to my logo design colours. I need the design to be easy to follow and to appeal to a younger audience (20's to mid 30's).
The target audience is pregnant mothers-to-be wishing to receive massage treatments, and new parents and grandparents of small babies that would like to learn how to massage their babies.
The look and feel should be modern, professional, elegant and feminine.
I need the design to be in a standard format such that I can update the content by myself ( and does not need specialised software) as the company and business progresses.

Target Market(s)

Contact Information for Business Card

Card should have rounded edges. Design should have the same "feel" as the website. Contact Details of my business address, mobile phone, email and website should be included.

Font styles to use
Script

Requirements
Must have
• Same colours as logo design. In cmyk system, the colours are: 20,60,0,0 which best result is pantone 681 and 40,40,0,0 which best result is pantone 2645. Card should include the logo design.

```html
<!DOCTYPE html>
<html lang="en">
<head>
<meta charset="utf-8">
<title>Willow Cradle Pregnancy and Baby Massage</title>
<link href="https://fonts.googleapis.com/css2?family=Open+Sans:wght@400;600;700&display=swap" rel="stylesheet">
<style>
:root{
  --plum:#b766a9;
  --plum-dark:#a4579a;
  --lilac:#8c6fb0;
  --ink:#3c3c3c;
  --muted:#5a5a5a;
  --rule:#c9c9c9;
  --white:#ffffff;
}
*{margin:0;padding:0;box-sizing:border-box}
html,body{width:857px;height:1200px;overflow:hidden;background:var(--white)}
body{position:relative;font-family:"Open Sans",sans-serif;color:var(--ink)}
.site-header{position:absolute;left:0;top:0;width:857px;height:86px;background:var(--white);z-index:3}
.brand-tab{position:absolute;left:48px;top:0;width:184px;height:142px;z-index:2}
.brand-name{position:absolute;left:66px;top:30px;width:148px;text-align:center;font-size:11.5px;font-weight:600;line-height:1.3;color:var(--plum);z-index:4}
.brand-dot{display:block;width:18px;height:18px;border-radius:50%;background:var(--plum);margin:0 auto 5px}
.search{position:absolute;left:482px;top:19px;width:141px;height:19px;border:1px solid #555;font-size:10px;font-weight:600;padding:1px 9px;color:var(--ink)}
.search svg{position:absolute;right:10px;top:4px}
.account{position:absolute;left:652px;top:24px;font-size:10px;font-weight:600;color:var(--ink);display:flex;align-items:center;gap:5px}
.cart{position:absolute;left:772px;top:24px}
.nav{position:absolute;top:56px;left:0;font-size:10.5px;font-weight:600;letter-spacing:.1px}
.nav span{position:absolute;white-space:nowrap;color:var(--ink)}
.nav .active{color:var(--plum)}
.hero{position:absolute;left:0;top:86px;width:857px;height:386px;background:radial-gradient(ellipse at 60% 50%,#c79a8e 0%,#9e7a7f 55%,#7c6470 100%)}
.hero-title{position:absolute;left:68px;top:210px;font-size:35px;font-weight:700;line-height:1.18;color:var(--white);text-shadow:0 2px 4px rgba(0,0,0,.35);z-index:2}
.hero-btn{position:absolute;left:70px;top:315px;width:88px;height:23px;background:var(--plum);color:var(--white);font-size:11.5px;font-weight:700;display:flex;align-items:center;justify-content:center;z-index:2}
.dots{position:absolute;left:413px;top:430px;display:flex;gap:2px;z-index:2}
.dots i{width:6px;height:6px;border-radius:50%;border:1px solid var(--white)}
.dots i:first-child{background:var(--white)}
.rule{position:absolute;left:70px;width:716px;height:1px;background:var(--rule)}
.copy{position:absolute;left:0;width:857px;text-align:center;font-size:9.8px;line-height:16.5px;color:var(--muted)}
.feature{position:absolute;left:0;top:562px;width:857px;height:352px;background:radial-gradient(ellipse at 50% 55%,#d6ad9a 0%,#8a6a55 55%,#c7a27c 100%)}
.badge{position:absolute;left:72px;top:1046px;width:148px;height:84px}
.badge-mark{position:absolute;left:0;top:2px;width:64px;height:78px;border-radius:8px;background:#ead6e6}
.badge-text{position:absolute;left:73px;top:0;font-size:13px;line-height:17px;color:#888;font-weight:400}
.badge-text b{font-weight:400;color:var(--plum)}
.news-title{position:absolute;left:336px;top:1047px;font-size:12px;font-weight:600;color:var(--ink)}
.news-input{position:absolute;left:336px;top:1073px;width:235px;height:28px;border:1px solid #888;font-size:8px;padding:8px 11px;color:var(--muted)}
.news-btn{position:absolute;left:336px;top:1110px;width:82px;height:27px;background:var(--plum);color:var(--white);font-size:10.5px;font-weight:700;display:flex;align-items:center;justify-content:center}
.follow-title{position:absolute;left:690px;top:1047px;font-size:12px;font-weight:600;color:var(--ink)}
.social{position:absolute;top:1078px;width:26px;height:26px;border-radius:50%;background:var(--plum)}
.footer-note{position:absolute;left:0;top:1173px;width:857px;text-align:center;font-size:9.6px;color:var(--muted)}
</style>
</head>
<body>
<header class="site-header">
  <div class="search">Search
    <svg width="9" height="9" viewBox="0 0 10 10"><circle cx="4" cy="4" r="3" fill="none" stroke="#333" stroke-width="1.5"/><line x1="6.2" y1="6.2" x2="9.2" y2="9.2" stroke="#333" stroke-width="1.6"/></svg>
  </div>
  <div class="account">
    <svg width="8" height="9" viewBox="0 0 8 9"><circle cx="4" cy="2.3" r="2.2" fill="#b766a9"/><path d="M0 9c0-3 1.8-4.3 4-4.3S8 6 8 9z" fill="#b766a9"/></svg>
    REGISTER / LOGIN
  </div>
  <svg class="cart" width="13" height="10" viewBox="0 0 13 10"><path d="M0 1h2l1.6 5.5h6.4L11.5 2.5H3" fill="none" stroke="#b766a9" stroke-width="1.4"/><circle cx="4.5" cy="8.7" r="1" fill="#b766a9"/><circle cx="9" cy="8.7" r="1" fill="#b766a9"/></svg>
  <nav class="nav">
    <span class="active" style="left:222px">HOME</span>
    <span style="left:274px">ABOUT ME</span>
    <span style="left:351px">PREGNANCY MASSAGE</span>
    <span style="left:489px">BABY MASSAGE</span>
    <span style="left:590px">PRICING &#8964;</span>
    <span style="left:666px">NEWS</span>
    <span style="left:718px">CONTACT ME</span>
  </nav>
</header>

<svg class="brand-tab" viewBox="0 0 184 142" aria-hidden="true"><path d="M0 86 L0 0 L184 0 L184 86 L102 138 Q92 144 82 138 Z" fill="#ffffff"/></svg>
<div class="brand-name"><span class="brand-dot"></span>Willow Cradle<br>Pregnancy and Baby<br>Massage</div>

<section class="hero" role="img" aria-label="Photo of two sleeping newborn twins wrapped in a peach cloth on a lace heart">
</section>
<h1 class="hero-title">Save Upto $ 50 by<br>online Booking</h1>
<div class="hero-btn">Book Now</div>
<div class="dots"><i></i><i></i><i></i><i></i></div>

<div class="rule" style="top:472px"></div>
<p class="copy" style="top:494px">Willow Cradle Pregnancy and Baby Massage was launched in 2017, offering massage for pregnant women, and<br>instruction of baby massage to parents, grandparents and carers.</p>

<section class="feature" role="img" aria-label="Photo of newborn twins sleeping together in a woolly nest basket"></section>

<p class="copy" style="top:936px">My vision is to provide a professional massage service to pregnant mothers and babies that also benefits from my skills and experience as a midwife.<br>My expectation is that after each session, my clients should leave feeling relaxed, calm, emotionally nurtured, soothed and supported.<br>At all times, I will take the utmost care of your privacy, safety and comfort in what is a very personal, intimate time in your life.</p>

<div class="badge">
  <div class="badge-mark" role="img" aria-label="Certification badge"></div>
  <div class="badge-text">Certified by<br><b>Cradle Touch</b><br><b>Massage</b><br>Guild</div>
</div>

<h2 class="news-title">SUBSCRIBE TO OUR NEWSLETTER</h2>
<div class="news-input">Enter Your Mail Id</div>
<div class="news-btn">SUBSCRIBE</div>

<h2 class="follow-title">FOLLOW US ON</h2>
<span class="social" style="left:692px" aria-label="Social link"></span>
<span class="social" style="left:725px" aria-label="Social link"></span>
<span class="social" style="left:758px" aria-label="Social link"></span>

<div class="rule" style="top:1160px"></div>
<p class="footer-note">© 2017 Willow Cradle Pregnancy and Baby Massage. All Rights Reserved.</p>
</body>
</html>
```